All-Natural Head Lice Removal company

I need a business card with my pre-existing logo. We are a new company located in Portland Oregon that goes into peoples homes to help with head lice removal. My products and approach are all- natural and also will be around children.On my current logo we used Teal Bl and the color Green. I am open to new ideas just want it simple and creative

Target Market(s)

my biggest market is families of school aged children

Industry/Entity Type

Business

Contact Information for Business Card

see upload for details from previous business card

Font styles to use
Serif

Colors
33a6d7
9bcb3b
f37122

Requirements
Must have
• Basic information/ logo put into a creative format that is catching to the eye
Nice to have
• creative

```html
<!DOCTYPE html>
<html lang="en">
<head>
<meta charset="utf-8">
<title>Nit Nest – Business Card</title>
<link rel="stylesheet" href="https://fonts.googleapis.com/css2?family=Arvo:wght@400;700&family=Open+Sans:wght@600&display=swap">
<style>
  :root {
    --page: #e9e7e3;
    --card: #ffffff;
    --ink: #2b2b2b;
    --blue: #33a6d7;
    --green: #9bcb3b;
    --black: #1d1d1d;
    --rule: #3a3a3a;
  }
  * { box-sizing: border-box; margin: 0; padding: 0; }
  html, body { width: 1200px; height: 913px; overflow: hidden; background: var(--page); }
  body { position: relative; font-family: "Arvo", Georgia, serif; color: var(--ink); }

  .card {
    position: absolute;
    width: 520px; height: 297px;
    background: var(--card);
    border-radius: 18px;
    overflow: hidden;
    box-shadow: 0 6px 18px rgba(0,0,0,.18);
  }
  .card-front { left: 70px; top: 120px; }
  .card-back  { left: 610px; top: 480px; }
  .card-shapes { position: absolute; inset: 0; width: 100%; height: 100%; }

  .brand { position: absolute; display: flex; align-items: center; gap: 10px; }
  .brand-dot { width: 46px; height: 46px; border-radius: 50%; background: var(--green); }
  .brand-name { font-family: "Arvo", Georgia, serif; font-weight: 700; font-size: 30px; color: var(--ink); }

  .front-brand { left: 28px; top: 100px; }
  .tagline { position: absolute; left: 190px; top: 38px; font-size: 13px; }
  .person { position: absolute; right: 40px; top: 96px; text-align: right; }
  .person-name { font-size: 17px; letter-spacing: .5px; text-transform: uppercase; }
  .person-role { font-size: 10px; color: var(--blue); text-transform: uppercase; letter-spacing: 1px; margin-top: 6px; }
  .name-rule { position: absolute; left: 190px; right: 0; top: 122px; height: 1px; background: var(--rule); }
  .contact-rule { position: absolute; left: 24px; width: 230px; top: 178px; height: 1px; background: var(--rule); }
  .contacts { position: absolute; left: 30px; top: 188px; list-style: none;
    font-family: "Open Sans", Arial, sans-serif; font-weight: 600; font-size: 14px; line-height: 21px; }
  .contacts li { display: flex; align-items: center; gap: 8px; }
  .contacts svg { width: 11px; height: 11px; fill: var(--blue); flex: none; }

  .back-brand { right: 40px; top: 50px; }
  .back-copy { position: absolute; left: 30px; top: 180px; font-weight: 700; font-size: 12.5px; line-height: 17px; }
  .back-url { position: absolute; left: 30px; top: 262px; font-size: 13px; color: #fff; }
</style>
</head>
<body>

<section class="card card-front" aria-label="Card front">
  <svg class="card-shapes" viewBox="0 0 520 297" aria-hidden="true">
    <rect x="0" y="265" width="520" height="32" fill="var(--blue)"/>
    <path d="M345 297 L345 268 C372 268 378 212 412 212 L520 212 L520 297 Z" fill="var(--black)"/>
  </svg>
  <p class="tagline">All Natural In-Home Lice Removal Services</p>
  <div class="brand front-brand">
    <span class="brand-dot"></span>
    <span class="brand-name">Nit Nest</span>
  </div>
  <div class="person">
    <p class="person-name">Carla Wendell</p>
    <p class="person-role">Owner</p>
  </div>
  <div class="name-rule"></div>
  <div class="contact-rule"></div>
  <ul class="contacts">
    <li><svg viewBox="0 0 12 12"><path d="M2.5 0.5 L4.5 0.5 L5 3.5 L3.6 4.4 C4.3 6 5.8 7.6 7.6 8.4 L8.5 7 L11.5 7.5 L11.5 9.5 C11.5 10.8 10.6 11.5 9.5 11.5 C4.5 11 1 7.5 0.5 2.5 C0.5 1.4 1.2 0.5 2.5 0.5 Z"/></svg>1-800-555-0199</li>
    <li><svg viewBox="0 0 12 12"><path d="M0.5 2 H11.5 V10 H0.5 Z M1.5 3 V3.4 L6 6.6 L10.5 3.4 V3 Z" fill-rule="evenodd"/></svg>Carla@NitNest.com</li>
    <li><svg viewBox="0 0 12 12"><circle cx="6" cy="6" r="5.5"/></svg>www.NitNest.com</li>
  </ul>
</section>

<section class="card card-back" aria-label="Card back">
  <svg class="card-shapes" viewBox="0 0 520 297" aria-hidden="true">
    <rect x="200" y="226" width="320" height="34" fill="var(--blue)"/>
    <path d="M0 226 L165 226 C195 226 198 260 230 260 L230 297 L0 297 Z" fill="var(--black)"/>
  </svg>
  <div class="brand back-brand">
    <span class="brand-dot"></span>
    <span class="brand-name">Nit Nest</span>
  </div>
  <p class="back-copy">Try Nit Nest Today and Be Lice Free Tomorrow!<br>All Natural In-Home Lice Removal Services</p>
  <p class="back-url">www.NitNest.com</p>
</section>

</body>
</html>
```